Larkfield Ridge Management

I need a professional website. My current website is larkfieldridgemanagement.com and I hate it. It was created with some AI tool very quickly because I needed a site up and running with no advanced notice. I’m open to all designs .. I trust you, the professionals will deliver the results I’m anxiously awaiting! :)

```html
<!DOCTYPE html>
<html lang="en">
<head>
<meta charset="utf-8">
<title>Larkfield Ridge Management — Who We Are</title>
<link href="https://fonts.googleapis.com/css2?family=Montserrat:wght@700;800;900&family=Inter:wght@400;500;600;700&display=swap" rel="stylesheet">
<style>
  :root {
    --navy: #1c2a44;
    --red: #c8232c;
    --ink: #444b57;
    --muted: #7a8599;
    --paper: #ffffff;
    --mist: #f5f7fa;
    --rule: #5c6270;
  }
  * { box-sizing: border-box; margin: 0; padding: 0; }
  html, body { width: 885px; height: 1200px; overflow: hidden; background: var(--paper); }
  body { position: relative; font-family: "Inter", sans-serif; color: var(--ink); }

  /* Header */
  .site-header { position: absolute; left: 0; top: 0; width: 885px; height: 52px; background: var(--paper); }
  .nav-link { position: absolute; top: 21px; font: 600 6.6px/1 "Inter", sans-serif; letter-spacing: 1.1px; color: var(--navy); text-transform: uppercase; }
  .brand { position: absolute; left: 412px; top: 12px; width: 62px; height: 28px; display: flex; align-items: center; justify-content: center; gap: 3px; font: 800 8px/1 "Montserrat", sans-serif; color: var(--navy); letter-spacing: .4px; white-space: nowrap; }
  .brand-dot { width: 6px; height: 6px; background: var(--red); flex: none; }
  .cta { position: absolute; left: 545px; top: 13px; width: 107px; height: 25px; background: var(--red); box-shadow: 2px 2px 0 var(--navy); color: #fff; font: 700 6.6px/25px "Inter", sans-serif; letter-spacing: 1px; text-align: center; }
  .strip { position: absolute; left: 0; top: 52px; width: 885px; height: 14px; background: var(--mist); }

  /* Hero */
  .hero { position: absolute; left: 0; top: 66px; width: 885px; height: 372px; background: var(--paper); overflow: hidden; }
  .hero-photo { position: absolute; inset: 0; }
  .eyebrow { position: absolute; left: 162px; top: 61px; display: flex; align-items: center; gap: 8px; font: 700 6.6px/1 "Montserrat", sans-serif; letter-spacing: 1.6px; color: var(--navy); }
  .eyebrow::before { content: ""; width: 22px; height: 2px; background: var(--red); }
  .hero-title { position: absolute; left: 162px; top: 82px; font: 900 31.5px/35px "Montserrat", sans-serif; color: var(--navy); letter-spacing: -.6px; }
  .hero-title em { font-style: normal; color: var(--red); }
  .hero-quote { position: absolute; left: 162px; top: 269px; width: 310px; height: 44px; border-left: 2px solid var(--red); padding: 8px 0 0 11px; font: 500 9.4px/15px "Inter", sans-serif; color: #4a5060; background: linear-gradient(90deg, #fff 88%, #e9ebee 100%); }
  .hero-base { position: absolute; left: 0; top: 438px; width: 885px; height: 4px; background: var(--navy); }

  /* Philosophy */
  .philosophy { position: absolute; left: 0; top: 442px; width: 885px; height: 362px; background: var(--mist); border-bottom: 2px solid var(--navy); }
  .story-card { position: absolute; left: 162px; top: 44px; width: 321px; height: 273px; background: #fff; border: 1px solid var(--navy); box-shadow: 4px 4px 0 var(--navy); padding: 23px 20px 0 22px; }
  .kicker { font: 800 6.2px/1 "Montserrat", sans-serif; color: var(--red); }
  .story-title { margin-top: 9px; font: 900 16px/21px "Montserrat", sans-serif; color: var(--navy); }
  .story-card p { margin-top: 11px; font: 400 7.3px/12px "Inter", sans-serif; letter-spacing: -.05px; color: var(--ink); }
  .story-card p + p { margin-top: 11px; }
  .photo-card { position: absolute; left: 498px; top: 44px; width: 224px; height: 179px; background: #fff; border: 1px solid var(--navy); box-shadow: 3px 3px 0 var(--navy); padding: 4px; }
  .photo-fill { width: 100%; height: 100%; background: linear-gradient(135deg, #cfcfcf 0%, #8d8d8d 45%, #e6e6e6 100%); }
  .stat-card { position: absolute; left: 498px; top: 238px; width: 224px; height: 79px; background: var(--navy); box-shadow: 3px 3px 0 var(--red); padding: 19px 19px; }
  .stat-value { font: 900 28px/1 "Montserrat", sans-serif; color: var(--red); }
  .stat-label { margin-top: 4px; font: 700 6.4px/1 "Inter", sans-serif; letter-spacing: 1.5px; color: #fff; }

  /* Values */
  .values { position: absolute; left: 0; top: 806px; width: 885px; height: 328px; background: #fff; }
  .values-rule { position: absolute; left: 431px; top: 43px; width: 22px; height: 2px; background: var(--red); }
  .values-kicker { position: absolute; left: 0; width: 885px; top: 53px; text-align: center; font: 800 6.2px/1 "Montserrat", sans-serif; color: var(--navy); }
  .values-title { position: absolute; left: 0; width: 885px; top: 69px; text-align: center; font: 900 16.5px/1 "Montserrat", sans-serif; color: var(--navy); }
  .value-card { position: absolute; top: 117px; width: 177px; height: 167px; background: #fff; border: 1px solid var(--navy); box-shadow: 2px 2px 0 var(--navy); padding: 15px 12px 0 15px; }
  .value-icon { width: 37px; height: 37px; background: var(--red); box-shadow: 2px 2px 0 var(--navy); display: flex; align-items: center; justify-content: center; }
  .value-title { margin-top: 23px; font: 900 10.7px/14.5px "Montserrat", sans-serif; color: var(--navy); }
  .value-body { margin-top: 7px; font: 400 7.3px/12px "Inter", sans-serif; letter-spacing: -.05px; color: var(--ink); }

  /* Footer */
  .footer-rule { position: absolute; left: 0; top: 1134px; width: 885px; height: 4px; background: var(--rule); }
  .site-footer { position: absolute; left: 0; top: 1138px; width: 885px; height: 62px; background: var(--navy); }
  .footer-brand { position: absolute; left: 148px; top: 26px; display: flex; align-items: center; gap: 3px; font: 800 5.6px/1 "Montserrat", sans-serif; color: #fff; white-space: nowrap; }
  .footer-brand .brand-dot { width: 5px; height: 5px; }
  .footer-divider { position: absolute; left: 200px; top: 22px; width: 1px; height: 16px; background: #3a4761; }
  .footer-text { position: absolute; top: 26px; font: 600 5.6px/7.5px "Inter", sans-serif; letter-spacing: .9px; text-transform: uppercase; }
  .footer-text.dim { color: #5d6b85; }
  .footer-text.soft { color: #b9c0cd; }
  .footer-text.bright { color: #fff; }
</style>
</head>
<body>
  <header class="site-header">
    <a class="nav-link" style="left:285px">Services</a>
    <a class="nav-link" style="left:340px">Why Larkfield</a>
    <div class="brand"><span class="brand-dot"></span>LARKFIELD</div>
    <a class="nav-link" style="left:489px">Contact</a>
    <a class="cta">REQUEST PROPOSAL</a>
  </header>
  <div class="strip"></div>

  <section class="hero">
    <svg class="hero-photo" width="885" height="372" viewBox="0 0 885 372">
      <defs>
        <linearGradient id="officeTone" x1="0" y1="0" x2="0" y2="1">
          <stop offset="0" stop-color="#242b38"/>
          <stop offset="0.5" stop-color="#4a5468"/>
          <stop offset="1" stop-color="#2f3748"/>
        </linearGradient>
      </defs>
      <polygon points="530,0 885,0 885,372 443,372" fill="url(#officeTone)" role="img" aria-label="Photo of a modern open-plan office with desks, toned in navy"/>
    </svg>
    <div class="eyebrow">WHO WE ARE</div>
    <h1 class="hero-title">REDEFINING<br>PROPERTY<br>MANAGEMENT<br>IN <em>NORTHEAST</em><br><em>OHIO.</em></h1>
    <p class="hero-quote">We don't just collect rent. We engineer long-term asset preservation.</p>
  </section>
  <div class="hero-base"></div>

  <section class="philosophy">
    <article class="story-card">
      <div class="kicker">OUR PHILOSOPHY</div>
      <h2 class="story-title">A TRUE PARTNER,<br>NOT JUST A VENDOR</h2>
      <p>Founded on the principles of financial transparency and operational excellence, Larkfield Ridge Management LLC was built to solve the biggest problem in real estate: a lack of reliable, professional boots on the ground.</p>
      <p>For too long, investors in the Cleveland and Akron markets have had to settle for property managers who are reactive, disorganized, and treat properties like transactions. We take a different approach. We apply rigorously tested, corporate-level frameworks to everyday property management.</p>
      <p>Whether you are an out-of-state investor needing a trusted guardian for your capital, or a local owner looking to scale, our mission is simple: to safeguard your property's value, maximize your monthly yield, and elevate the tenant experience to reduce turnover.</p>
    </article>
    <div class="photo-card"><div class="photo-fill" role="img" aria-label="Black and white photo of two colleagues celebrating at a meeting table"></div></div>
    <div class="stat-card">
      <div class="stat-value">100%</div>
      <div class="stat-label">COMMITMENT TO ASSET PRESERVATION</div>
    </div>
  </section>

  <section class="values">
    <div class="values-rule"></div>
    <div class="values-kicker">CORE VALUES</div>
    <h2 class="values-title">ENGINEERING EXCELLENCE</h2>

    <article class="value-card" style="left:162px">
      <div class="value-icon">
        <svg width="18" height="18" viewBox="0 0 24 24" fill="none" stroke="#fff" stroke-width="2"><path d="M2 12s3.5-7 10-7 10 7 10 7-3.5 7-10 7S2 12 2 12z"/><circle cx="12" cy="12" r="3"/></svg>
      </div>
      <h3 class="value-title">RADICAL<br>TRANSPARENCY</h3>
      <p class="value-body">Real-time data, clear financial statements, and honest communication. You will never have to guess how your asset is performing.</p>
    </article>

    <article class="value-card" style="left:354px">
      <div class="value-icon">
        <svg width="17" height="17" viewBox="0 0 24 24" fill="none" stroke="#fff" stroke-width="2" stroke-linejoin="round"><path d="M12 2l8 3v6c0 5-3.5 9-8 11-4.5-2-8-6-8-11V5l8-3z"/></svg>
      </div>
      <h3 class="value-title">ASSET PRESERVATION</h3>
      <p class="value-body">We treat your real estate like our own portfolio. Preventative maintenance today saves thousands in capital expenditures tomorrow.</p>
    </article>

    <article class="value-card" style="left:546px">
      <div class="value-icon">
        <svg width="18" height="18" viewBox="0 0 24 24" fill="none" stroke="#fff" stroke-width="2" stroke-linecap="round"><circle cx="9" cy="8" r="3.5"/><path d="M3 20c0-3.5 2.7-6 6-6s6 2.5 6 6"/><path d="M15 4.5a3.5 3.5 0 0 1 0 7"/><path d="M18 14.5c2 .8 3 2.8 3 5.5"/></svg>
      </div>
      <h3 class="value-title">TENANT RETENTION</h3>
      <p class="value-body">A vacant unit is a liability. We foster respectful, responsive relationships with tenants to ensure steady, long-term occupancy.</p>
    </article>
  </section>

  <div class="footer-rule"></div>
  <footer class="site-footer">
    <div class="footer-brand"><span class="brand-dot"></span>LARKFIELD</div>
    <div class="footer-divider"></div>
    <div class="footer-text soft" style="left:210px">© 2026. ALL RIGHTS<br>RESERVED.</div>
    <div class="footer-text dim" style="left:327px">PROUDLY SERVING GREATER CLEVELAND &amp; AKRON,<br>OHIO</div>
    <div class="footer-text soft" style="left:524px">PRIVACY</div>
    <div class="footer-text soft" style="left:568px">TERMS</div>
    <div class="footer-text bright" style="left:604px">OWNER<br>PORTAL</div>
    <div class="footer-text bright" style="left:669px">TENANT<br>PORTAL</div>
  </footer>
</body>
</html>
```